Medical VIP club - small design

Please read the specs in a design brief attached. Also we don't have logo in a Vector format and attaching the only version we have.

Club

```html
<!DOCTYPE html>
<html lang="en">
<head>
<meta charset="utf-8">
<title>Vitalora – Services</title>
<link href="https://fonts.googleapis.com/css2?family=Arimo:wght@400;700&display=swap" rel="stylesheet">
<style>
  :root {
    --navy-deep: #132a6b;
    --navy: #1d3a86;
    --navy-light: #2e4f9e;
    --sky: #1e84f0;
    --sky-light: #4aa6ff;
    --tab-active: #0a20b8;
    --strip: #a9c9f2;
    --title-top: #5d6690;
    --title-bottom: #3a4474;
    --th-top: #5b55b8;
    --th-bottom: #3e3a96;
    --rule: #c9c9c9;
    --text: #333;
    --white: #fff;
    --brand: #39b3f0;
  }
  * { box-sizing: border-box; margin: 0; padding: 0; }
  html, body { width: 1200px; height: 876px; overflow: hidden; }
  body { font-family: "Arimo", Arial, sans-serif; background: var(--navy); position: relative; }

  .site-header {
    position: absolute; left: 0; top: 0; width: 1200px; height: 280px;
    background: linear-gradient(180deg, #1a3276 0%, var(--navy-light) 55%, var(--navy) 100%);
  }
  .brand {
    position: absolute; left: 42px; top: 78px;
    display: flex; align-items: center; gap: 14px;
    font-size: 62px; font-weight: 700; color: var(--brand);
  }
  .brand-dot { width: 40px; height: 40px; border-radius: 50%; background: var(--brand); }
  .phone { position: absolute; left: 788px; top: 50px; display: flex; align-items: center; gap: 20px; }
  .phone-number { font-size: 46px; font-weight: 700; color: var(--white); letter-spacing: -1px; }

  .nav-strip { position: absolute; left: 0; top: 241px; width: 1200px; height: 38px; background: var(--strip); }
  .main-nav { position: absolute; left: 24px; top: 208px; display: flex; gap: 4px; }
  .main-nav a {
    width: 190px; height: 71px; border-radius: 14px 14px 0 0;
    background: linear-gradient(180deg, var(--sky-light) 0%, var(--sky) 48%, #0d6ce0 52%, var(--sky) 100%);
    color: var(--white); text-decoration: none; font-size: 20px;
    display: flex; align-items: center; justify-content: center; padding-top: 6px;
  }
  .main-nav a.is-active { background: linear-gradient(180deg, #2340d8 0%, var(--tab-active) 55%, #0818a0 100%); }

  .content-panel {
    position: absolute; left: 24px; top: 289px; width: 1156px; height: 485px;
    background: var(--white); border: 1px solid #9fb0d8;
  }
  .page-title {
    margin: 6px 6px 0; height: 54px; padding-left: 15px;
    background: linear-gradient(180deg, var(--title-top), var(--title-bottom));
    color: var(--white); font-size: 24px; font-weight: 400;
    display: flex; align-items: center;
  }
  .packages { position: absolute; left: 19px; top: 81px; width: 1110px; border-collapse: collapse; font-size: 14px; color: var(--text); }
  .packages th {
    height: 35px; background: linear-gradient(180deg, var(--th-top), var(--th-bottom));
    color: var(--white); font-size: 15px; font-weight: 700; border-right: 1px solid #9c98d8;
  }
  .packages td { height: 35.5px; border: 1px solid var(--rule); padding-left: 14px; }
  .packages td:first-child { padding-left: 25px; }
  .packages tr.price td { border: none; text-align: center; font-weight: 700; font-size: 14px; height: 46px; padding: 0; }
  .packages col.c1 { width: 363px; } .packages col.c2 { width: 387px; }

  .site-footer {
    position: absolute; left: 0; top: 781px; width: 1200px; height: 95px;
    background: linear-gradient(180deg, var(--navy-light) 0%, var(--navy) 60%, var(--navy-deep) 100%);
    border-top: 1px solid #5d78c0;
  }
  .social { position: absolute; left: 25px; top: 31px; display: flex; gap: 6px; }
  .social span { width: 36px; height: 36px; border-radius: 4px; }
  .social .s1 { background: #3b5ba0; } .social .s2 { background: #55bde8; } .social .s3 { background: #f07d22; }
  .copyright { position: absolute; left: 0; width: 1200px; top: 49px; text-align: center; font-size: 12px; color: var(--white); }
  .footer-brand { position: absolute; right: 22px; top: 28px; font-size: 36px; font-weight: 700; color: var(--brand); }
</style>
</head>
<body>
  <header class="site-header">
    <div class="brand"><span class="brand-dot"></span>Vitalora</div>
    <div class="phone">
      <svg width="104" height="104" viewBox="0 0 104 104" aria-hidden="true">
        <defs>
          <radialGradient id="orb" cx="40%" cy="30%" r="70%">
            <stop offset="0" stop-color="#4d7fe0"/><stop offset="1" stop-color="#0b1f66"/>
          </radialGradient>
        </defs>
        <circle cx="52" cy="52" r="50" fill="url(#orb)" stroke="#8fb0ee" stroke-width="2"/>
        <path d="M26 46 Q52 24 78 46 L72 54 L64 50 L64 44 Q52 38 40 44 L40 50 L32 54 Z" fill="#fff"/>
        <path d="M36 56 L68 56 L76 74 L28 74 Z" fill="#fff"/>
        <circle cx="52" cy="64" r="5" fill="#1d3a86"/>
      </svg>
      <span class="phone-number">555-010-010</span>
    </div>
    <div class="nav-strip"></div>
    <nav class="main-nav">
      <a href="#">About Us</a>
      <a href="#">VIP Club</a>
      <a href="#">Services</a>
      <a href="#">Packages &amp; Prices</a>
      <a href="#" class="is-active">Registration</a>
      <a href="#">Contacts</a>
    </nav>
  </header>

  <main class="content-panel">
    <h1 class="page-title">Services</h1>
    <table class="packages">
      <colgroup><col class="c1"><col class="c2"><col></colgroup>
      <thead><tr><th>Package 1</th><th>Package 2</th><th>Package 3</th></tr></thead>
      <tbody>
        <tr><td>-Lorem ipsum</td><td>-Lorem ipsum</td><td>-Lorem ipsum</td></tr>
        <tr><td>-Lorem ipsum</td><td>-Lorem ipsum</td><td>-Lorem ipsum</td></tr>
        <tr><td>-Lorem ipsum</td><td>-Lorem ipsum</td><td>-Lorem ipsum</td></tr>
        <tr><td>-Lorem ipsum</td><td>-Lorem ipsum</td><td>-Lorem ipsum</td></tr>
        <tr><td>-Lorem ipsum</td><td>-Lorem ipsum</td><td>-Lorem ipsum</td></tr>
        <tr><td>-Lorem ipsum</td><td>-Lorem ipsum</td><td>-Lorem ipsum</td></tr>
        <tr><td>-Lorem ipsum</td><td>-Lorem ipsum</td><td>-Lorem ipsum</td></tr>
        <tr><td>-Lorem ipsum</td><td>-Lorem ipsum</td><td>-Lorem ipsum</td></tr>
        <tr><td>-Lorem ipsum</td><td>-Lorem ipsum</td><td>-Lorem ipsum</td></tr>
        <tr class="price"><td>$000</td><td>$000</td><td>$000</td></tr>
      </tbody>
    </table>
  </main>

  <footer class="site-footer">
    <div class="social"><span class="s1"></span><span class="s2"></span><span class="s3"></span></div>
    <p class="copyright">Copyright ©2010 Vitalora. All Rights Reserved</p>
    <div class="footer-brand">Vitalora</div>
  </footer>
</body>
</html>
```